Creation of a construction/bricklaying business website

Following the template format of "Halloway 7", the following content would need to be included:
1. Landing page with 3 tiles that go to their own pages.
- Landing page to include background photo and description of services offered.
2. 3 tiles to include:
a) "Contact Us For A Free Quote or Friendly Discussion" Form (middle tile)
b) Case Studies and Testimonials
c) Certifications and Professional Membership
- Design logo to be used from previous SketchNestle project. Example of logo attached below, please access full JPG files from our account.

Target Market(s)

Prospective clients seeking construction work (bricklaying speciality)

Industry/Entity Type

Residential Construction

Coding

Coded - Design and coding required

Number of Pages Required

4 page

Font styles to use
Sans Serif

Colors

Designer to choose colors to be used in the design.

Requirements
Must have
• Following the template format of "Halloway 7", the following content would need to be included:
• 1. Landing parent page with 3 tiles that go to the 3 child pages.
• - Landing page to include background photo and description of services offered.
• 2. 3 tiles to include:
• a) "Contact Us For A Free Quote or Friendly Discussion" Form (middle tile)
• b) Case Studies and Testimonials (first tile / left side)
• c) Certifications and Professional Memberships (third tile / right side) (This should include logos of the relevant organisations being displayed. Specifically GQT and the Pillar Seal GQT).
• - Design logo to be used from previous SketchNestle project. Example of logo attached below, please access full JPG files from our account.
Nice to have
• Sleek and modern feel.
• Approachable in terms of how people can contact the company for a quote.
• Traditional pictures to give credibility and comfort around choosing this company.
Should not have
• Cheesy pictures
• Over-complicated
• Simple to use
• Easy URL domain name

```html
<!DOCTYPE html>
<html lang="en">
<head>
<meta charset="utf-8">
<title>R.T.Hale Construction Ltd</title>
<link rel="stylesheet" href="https://fonts.googleapis.com/css2?family=Open+Sans:wght@400;600;700&display=swap">
<style>
:root{
  --brand-blue:#0b3a8c;
  --hero-dark:#2a2a2a;
  --page-bg:#f4f4f4;
  --card-bg:#ffffff;
  --field-bg:#f1f1f1;
  --text-dark:#222;
  --text-muted:#8a8a8a;
  --footer-bg:#1c1c1c;
  --overlay:rgba(0,0,0,.72);
  --badge-red:#c8242b;
}
*{margin:0;padding:0;box-sizing:border-box}
html,body{width:1200px;height:1165px;overflow:hidden}
body{font-family:"Open Sans",Arial,sans-serif;background:var(--page-bg);position:relative;color:var(--text-dark)}
.hero{position:absolute;left:0;top:0;width:1200px;height:614px}
.hero-photo{position:absolute;inset:0;background:radial-gradient(ellipse at 55% 40%,#6a6660 0%,#3e3b38 45%,#1e1d1c 100%)}
.hero-brand{position:absolute;left:0;right:0;top:262px;text-align:center;color:#fff;font-size:44px;font-weight:700;letter-spacing:1px}
.hero-intro{position:absolute;left:231px;top:344px;color:#fff;font-size:14.4px;font-weight:400}
.service-list{position:absolute;top:380px;list-style:none;color:#fff;font-size:19px;font-weight:700}
.service-list li{height:32px}
.service-list li::before{content:"›";margin-right:8px}
.service-left{left:231px}
.service-right{right:233px;text-align:right}
.carousel-arrow{position:absolute;top:294px;width:20px;height:28px}
.arrow-prev{left:54px}.arrow-next{left:1126px}
.tiles{position:absolute;top:644px;left:132px;display:flex;gap:24px}
.tile{width:296px;height:404px;background:var(--card-bg);position:relative}
.tile-head{height:76px;display:flex;align-items:center;justify-content:center;text-align:center;color:var(--brand-blue);font-weight:700;font-size:16px;line-height:20px;padding:0 20px}
.tile-media{height:144px}
.media-work{background:linear-gradient(135deg,#c9643a,#e6b26a 55%,#7a4a30)}
.media-site{background:linear-gradient(180deg,#7f93a8,#3f4c5c)}
.media-badges{background:#fff;position:relative}
.badge-small{position:absolute;left:16px;top:30px;width:62px;height:90px;background:var(--badge-red);border-radius:3px}
.badge-large{position:absolute;left:100px;top:27px;width:182px;height:91px;border:3px solid var(--badge-red);border-radius:3px;background:#fff}
.badge-large span{position:absolute;left:8px;top:8px;width:50px;height:50px;background:var(--brand-blue);border-radius:50%}
.tile-title{padding:26px 14px 0;font-size:14.6px;font-weight:600;line-height:19px}
.tile-text{padding:10px 14px 0;font-size:10.4px;color:var(--text-muted);line-height:17.6px}
.tile-btn{position:absolute;left:14px;top:350px;height:33px;padding:0 18px;border:1px solid var(--brand-blue);color:var(--brand-blue);font-size:10.4px;line-height:31px;background:transparent}
.footer{position:absolute;left:0;top:1076px;width:1200px;height:89px;background:var(--footer-bg)}
.copyright{position:absolute;left:132px;top:36px;font-size:10.4px;color:#999}
.social{position:absolute;right:132px;top:34px;display:flex;gap:14px;font-size:11px;color:#999;font-weight:600}
.overlay{position:absolute;inset:0;background:var(--overlay)}
.quote-modal{position:absolute;left:312px;top:380px;width:576px;height:429px;background:#fff;padding:0 20px}
.modal-close{position:absolute;right:-11px;top:-11px;width:22px;height:22px}
.modal-title{text-align:center;color:var(--brand-blue);font-size:18px;font-weight:700;margin-top:17px;height:39px}
.quote-form{display:grid;grid-template-columns:264px 264px;gap:7px 8px}
.field{height:41px;background:var(--field-bg);display:flex;align-items:center;justify-content:space-between;padding:0 13px 0 15px;font-size:11.6px;color:#444;line-height:13px}
.field-wide{grid-column:1 / 3;height:112px;align-items:flex-start;padding-top:14px}
.submit{grid-column:1 / 3;justify-self:center;margin-top:11px;width:77px;height:33px;border:1px solid var(--brand-blue);background:#fff;color:var(--brand-blue);font-family:inherit;font-size:10.6px;font-weight:600}
</style>
</head>
<body>
<section class="hero">
  <div class="hero-photo" role="img" aria-label="Dark photo of a bricklayer at work on a building site"></div>
  <div class="hero-brand">R.T.Hale Construction Ltd</div>
  <p class="hero-intro">R.T.Hale Construction Ltd is a construction company that has expertise and experience in the following areas</p>
  <ul class="service-list service-left"><li>EXTENSIONS</li><li>NEW BUILDS</li></ul>
  <ul class="service-list service-right"><li>GROUNDWORK</li><li>DECORATIVE BRICKWORKS</li></ul>
  <svg class="carousel-arrow arrow-prev" viewBox="0 0 20 28"><path d="M15 2 4 14l11 12" fill="none" stroke="#999" stroke-width="2"/></svg>
  <svg class="carousel-arrow arrow-next" viewBox="0 0 20 28"><path d="M5 2l11 12L5 26" fill="none" stroke="#999" stroke-width="2"/></svg>
</section>

<section class="tiles">
  <article class="tile">
    <h2 class="tile-head">CASE STUDIES AND TESTIMONIALS</h2>
    <div class="tile-media media-work" role="img" aria-label="Close-up of hands laying bricks with mortar"></div>
    <h3 class="tile-title">Etiam mattis augue vehicula posuere, sit amet tempus lectus</h3>
    <p class="tile-text">Fusce eget neque elit. Sed augue orci, elementum in magna congue, tincidunt vulputate erat. Aliquam consectetur orci molestie dictum molestie.</p>
    <a class="tile-btn">View All</a>
  </article>
  <article class="tile">
    <h2 class="tile-head">CONTACT US FOR A FREE QUOTE</h2>
    <div class="tile-media media-site" role="img" aria-label="Building under construction with scaffolding"></div>
    <h3 class="tile-title">Cras eget leo nunc hendrerit ultricies eu at nisl</h3>
    <p class="tile-text">Fusce eget neque elit. Sed augue orci, elementum in magna congue, tincidunt vulputate erat. Aliquam consectetur orci molestie dictum molestie.</p>
    <a class="tile-btn">Contact Now</a>
  </article>
  <article class="tile">
    <h2 class="tile-head">CERTIFICATIONS AND PROFESSIONAL MEMBERSHIPS</h2>
    <div class="tile-media media-badges" role="img" aria-label="Membership badges of GQT and Pillar Seal GQT">
      <div class="badge-small"></div>
      <div class="badge-large"><span></span></div>
    </div>
    <h3 class="tile-title">Maecenas vel tortor accumsan quam varius imperdiet</h3>
    <p class="tile-text">Fusce eget neque elit. Sed augue orci, elementum in magna congue, tincidunt vulputate erat. Aliquam consectetur orci molestie dictum molestie.</p>
    <a class="tile-btn">Read More</a>
  </article>
</section>

<footer class="footer">
  <p class="copyright">Copyright © 2018 R.T.Hale Construction Ltd. &nbsp;All rights reserved.</p>
  <div class="social"><span>Chatter</span><span>Pulse</span></div>
</footer>

<div class="overlay"></div>

<section class="quote-modal">
  <svg class="modal-close" viewBox="0 0 22 22"><circle cx="11" cy="11" r="11" fill="#999"/><circle cx="11" cy="11" r="6" fill="#fff"/><path d="M8.6 8.6l4.8 4.8M13.4 8.6l-4.8 4.8" stroke="#777" stroke-width="1.6"/></svg>
  <h1 class="modal-title">CONTACT US FOR A FREE QUOTE OR FRIENDLY DISCUSSION</h1>
  <form class="quote-form">
    <div class="field">First name</div>
    <div class="field">Last name</div>
    <div class="field">Email Address</div>
    <div class="field">Contact Phone Number</div>
    <div class="field">Post code</div>
    <div class="field">Upload Image
      <svg width="14" height="11" viewBox="0 0 14 11"><path d="M0 1h5l1 1.5h6V4H3L0 10z" fill="#555"/><path d="M3 5h11l-3 6H0z" fill="#555"/></svg>
    </div>
    <div class="field">Ideal Budget
      <svg width="10" height="6" viewBox="0 0 10 6"><path d="M0 0h10L5 6z" fill="#444"/></svg>
    </div>
    <div class="field"><span>Ideal timeframe for job start and<br>completion dates</span>
      <svg width="13" height="13" viewBox="0 0 13 13"><rect x=".5" y="1.5" width="12" height="11" fill="none" stroke="#555"/><rect x=".5" y="1.5" width="12" height="2.5" fill="#555"/><path d="M3.5 4v8M6.5 4v8M9.5 4v8M.5 7h12M.5 10h12" stroke="#555" stroke-width=".8"/></svg>
    </div>
    <div class="field field-wide">Description of the job required</div>
    <button class="submit" type="button">Submit</button>
  </form>
</section>
</body>
</html>
```